MS word document templates for consultancy

I need the following templates for my business using my logo as branding.

- General report template
- Letter head template
- Tender proposal template

The templates should be sleek and with minimal colors, but with a small amount of green and grey where appropriate (as per attached logo and email signature). Font should be consistent with the text in the email signature.

```html
<!DOCTYPE html>
<html lang="en">
<head>
<meta charset="utf-8">
<title>Keel Onward Letterhead</title>
<link rel="stylesheet" href="https://fonts.googleapis.com/css2?family=Lato:wght@400;700&display=swap">
<style>
  :root {
    --brand-green: #2a9447;
    --ink: #101010;
    --paper: #ffffff;
  }
  * { margin: 0; padding: 0; box-sizing: border-box; }
  html, body { width: 848px; height: 1200px; overflow: hidden; background: var(--paper); }
  .letterhead {
    position: relative;
    width: 848px;
    height: 1200px;
    font-family: "Lato", Arial, sans-serif;
    background: var(--paper);
  }
  .frame { position: absolute; inset: 0; width: 848px; height: 1200px; }
  .frame .green { fill: var(--brand-green); }
  .frame .black { fill: var(--ink); }
  .brand-name {
    position: absolute;
    right: 83px;
    top: 104px;
    font-size: 44px;
    font-weight: 400;
    color: var(--ink);
    letter-spacing: 0.5px;
    line-height: 1;
  }
  .sender {
    position: absolute;
    left: 86px;
    top: 1022px;
  }
  .sender-name {
    font-size: 20px;
    font-weight: 700;
    color: var(--brand-green);
    line-height: 1.2;
  }
  .sender-role {
    margin-top: 9px;
    font-size: 20px;
    font-weight: 700;
    color: var(--ink);
    line-height: 1.2;
  }
  .contact {
    position: absolute;
    right: 87px;
    top: 1025px;
    display: flex;
    align-items: center;
    gap: 11px;
    color: var(--brand-green);
    font-size: 20px;
    font-weight: 700;
  }
  .contact svg { width: 27px; height: 27px; }
</style>
</head>
<body>
<div class="letterhead">
  <svg class="frame" viewBox="0 0 848 1200" aria-hidden="true">
    <polygon class="green" points="0,0 848,0 848,25 431,25 409,90 0,90"/>
    <polygon class="black" points="438,33 848,33 848,67 427,67"/>
    <polygon class="black" points="0,90 320,90 310,120 0,120"/>
    <polygon class="green" points="0,120 48,120 0,248"/>
    <polygon class="green" points="848,1050 848,1134 816,1134"/>
    <polygon class="black" points="522,1134 848,1134 848,1153 513,1153"/>
    <polygon class="black" points="0,1153 461,1153 451,1185 0,1185"/>
    <polygon class="green" points="468,1153 848,1153 848,1200 0,1200 0,1189 457,1189"/>
  </svg>

  <div class="brand-name">Keel Onward</div>

  <div class="sender">
    <p class="sender-name">Daniel Roper</p>
    <p class="sender-role">Managing Director</p>
  </div>

  <div class="contact">
    <svg viewBox="0 0 28 28" aria-hidden="true">
      <circle cx="14" cy="14" r="12.5" fill="none" stroke="currentColor" stroke-width="1.8"/>
      <path d="M10 7.5c.6-.4 1.3-.3 1.7.3l1.3 2.2c.3.6.2 1.2-.3 1.6l-.9.7c.5 1.6 1.6 3 3 4l.9-.6c.5-.4 1.2-.3 1.6.2l1.5 2c.4.6.3 1.3-.3 1.7l-1 .7c-.9.6-2.1.6-3-.1-2.9-2-5-4.9-5.9-8.3-.3-1 .1-2.1 1-2.7z" fill="currentColor"/>
    </svg>
    <span>0400 555 318</span>
  </div>
</div>
</body>
</html>
```